Investment company needing business card

We are wanting a business card which looks sharp and easy on the eye. We are thinking of having a business card with the logo embossed on it, to really make it stand out. We will only have a small amount of information of the business card, person's name, position, email address and phone number

Contact Information for Business Card

Danielle Frost
Executive Assistant
+64 21 473 5162
danielf@harwickpartners.co.nz

Requirements
Must have
• Embossed logo
Should not have
• Not to be busy

```html
<!DOCTYPE html>
<html lang="en">
<head>
<meta charset="utf-8">
<title>Harwick Partners – Business Card</title>
<link href="https://fonts.googleapis.com/css2?family=Open+Sans:wght@400;600;700&display=swap" rel="stylesheet">
<style>
  :root {
    --page: #e4e1de;
    --card-white: #ffffff;
    --slate: #666668;
    --green: #1fb36f;
    --text-dark: #4a4a4c;
    --text-light: #ffffff;
  }
  * { margin: 0; padding: 0; box-sizing: border-box; }
  html, body {
    width: 1200px; height: 997px; overflow: hidden;
    background: var(--page);
    font-family: "Open Sans", Arial, sans-serif;
  }
  .stage {
    position: relative; width: 1200px; height: 997px;
    display: flex; align-items: center; justify-content: center; gap: 40px;
  }
  .card {
    position: relative; width: 540px; height: 309px; overflow: hidden;
    box-shadow: 0 2px 6px rgba(0,0,0,.12);
  }
  .card-front { background: var(--card-white); }
  .card-back { background: var(--slate); }

  .front-waves { position: absolute; inset: 0; width: 100%; height: 100%; }

  .holder { position: absolute; left: 30px; top: 34px; color: var(--text-light); }
  .holder-name { font-size: 19px; font-weight: 700; line-height: 1.2; }
  .holder-role { font-size: 14px; font-weight: 400; }

  .contact-list {
    position: absolute; left: 30px; bottom: 30px; list-style: none;
    color: var(--text-dark); font-size: 14px; line-height: 1.7;
  }
  .contact-list li { display: flex; align-items: center; gap: 8px; }
  .contact-icon { width: 13px; height: 13px; flex: none; }

  .brand { display: flex; align-items: center; gap: 10px; }
  .brand-square { width: 26px; height: 26px; flex: none; }
  .brand-name { font-weight: 700; letter-spacing: 2px; text-transform: uppercase; }

  .brand-front { position: absolute; right: 30px; top: 132px; }
  .brand-front .brand-square { background: var(--green); }
  .brand-front .brand-name { color: var(--slate); font-size: 17px; }

  .back-content {
    position: absolute; inset: 0; display: flex; flex-direction: column;
    align-items: center; justify-content: center; gap: 60px; padding-top: 40px;
  }
  .brand-back .brand-square { background: var(--text-light); width: 30px; height: 30px; }
  .brand-back .brand-name {
    color: var(--text-light); font-size: 22px;
    border-bottom: 1px solid rgba(255,255,255,.7); padding-bottom: 4px;
  }
  .back-web { color: var(--text-light); font-size: 14px; letter-spacing: 3px; }
</style>
</head>
<body>
<main class="stage">
  <section class="card card-front" aria-label="Business card front">
    <svg class="front-waves" viewBox="0 0 540 309" aria-hidden="true">
      <path d="M0,0 H540 V16 C470,18 410,25 340,45 C260,70 150,108 0,110 Z" fill="var(--slate)"/>
      <path d="M0,124 C150,122 262,84 344,58 C414,38 472,30 540,28 V36 C474,38 418,46 348,66 C266,92 152,134 0,136 Z" fill="var(--green)"/>
      <path d="M0,144 C152,142 268,100 352,74 C420,54 476,46 540,42 V46 C478,50 424,58 356,78 C272,104 154,150 0,152 Z" fill="var(--slate)"/>
    </svg>
    <div class="holder">
      <p class="holder-name">Danielle Frost</p>
      <p class="holder-role">Executive Assistant</p>
    </div>
    <div class="brand brand-front">
      <span class="brand-square"></span>
      <span class="brand-name">Harwick Partners</span>
    </div>
    <ul class="contact-list">
      <li>
        <svg class="contact-icon" viewBox="0 0 13 13" aria-hidden="true"><rect width="13" height="13" rx="2" fill="var(--green)"/><path d="M4 3 L5.5 3 L6 5 L5 5.8 C5.5 7 6.2 7.6 7.2 8 L8 7 L10 7.5 L10 9 C6.5 9.3 3.7 6.5 4 3 Z" fill="#fff"/></svg>
        <span>+64 21 473 5162</span>
      </li>
      <li>
        <svg class="contact-icon" viewBox="0 0 13 13" aria-hidden="true"><rect width="13" height="13" rx="2" fill="var(--green)"/><rect x="3" y="4" width="7" height="5" fill="none" stroke="#fff" stroke-width="1"/><path d="M3 4 L6.5 7 L10 4" fill="none" stroke="#fff" stroke-width="1"/></svg>
        <span>danielf@harwickpartners.co.nz</span>
      </li>
      <li>
        <svg class="contact-icon" viewBox="0 0 13 13" aria-hidden="true"><rect width="13" height="13" rx="2" fill="var(--green)"/><circle cx="6.5" cy="6.5" r="3.5" fill="none" stroke="#fff" stroke-width="1"/><path d="M3 6.5 H10 M6.5 3 V10" stroke="#fff" stroke-width=".8"/></svg>
        <span>www.harwickpartners.co.nz</span>
      </li>
    </ul>
  </section>

  <section class="card card-back" aria-label="Business card back">
    <div class="back-content">
      <div class="brand brand-back">
        <span class="brand-square"></span>
        <span class="brand-name">Harwick Partners</span>
      </div>
      <p class="back-web">www.harwickpartners.co.nz</p>
    </div>
  </section>
</main>
</body>
</html>
```